Bold, Modern, Clean "Kestrelwaymassage.com" website

Why we stand out?
We are a male and female mobile massage team. Our names are Paul and Lina. 
Kestrel Way is a Seattle based mobile massage service. Our massage is offered to the community with a goal of facilitating balance within each individual. We specialize in integrated Pain management, and sports/medical massage therapy. Every client's first assessment is attended by our male and female massage therapist team. Depending on the goals identified for an individual determines which therapist will be assigned to provide treatment, if not both.

Our passion...
Here at Kestrel Way, we have a great passion for Postural Resoration and how it is integrated into an individual's Massage treatment. We pride ourselves in being natural facilitators of healing, which takes the ego of the therapist out of the client's healing process. We strive to deliver the best massage possible by including modalities such as Neuromuscular, Myofascial release, spontaneous muscle release, postural restoration, orthopedic, and medical massage.

Our education...

We are both Graduates of Venmora, school of massage therapy. We have continuing education in medical massage, myofacial release, trigger point therapy, postural restoration, anatomy, and spontaneous muscle release. Lina is also a Certified Yoga Instructor, which amplifies her experience with flexibility and strength as it pertains to each individual. Paul's passion is Massage, stretching, and strength training to encourage postural restoration and realignment.

Our rates-

Our rates are $75/ 60 minutes, $95/ 90 minutes, and $120/ 120 minutes.

Education-
Both Lina and I worked as behavioral health professionals that specialized in life skills mentoring for youth who had experienced different types of trauma. This led us both to want to help others in a different environment, where individuals can be empowered to take responsibility over their own healing. To us, massage is a type of manipulation physical therapy, that encourages healing on many levels.

Advice to any massage client-
The most important thing to 'us', as Licenced providers is to get you on to our table to show you our skills. But a good therapist never forgets that it's not about what we do for you, but what we can facilitate for you. Your health and healing has nothing to do with us. It is yours, not ours. Identify what your goals are with any Therapist, and know what the end looks like. Progress should be tangible, such as range of motion, and decreased pain.

Lina and Paul at Kestrel Way are awesome! I recently had open heart surgery, and Lina worked on me to increase my range of motion while helping with the pinched nerve from my arm being in the same position for so long during my surgery. My wife drives a lot for work, and Paul has helped decrease her neck and lower back pain immensely. They are seriously the best therapists I have ever worked with. I would recommend them to anyone who needs anything from stress relief to a medical massage treatment. They are professional, up beat, easy going, and always on time. And, I love that they meet us where ever we like! We did a staycation recently, where they came to our hotel to give us relaxation massages. Although usually they come to our home, where we focus on pain related issues. We will continue to work with them for a long, long time.

Target Market(s)

Mobile massage therapy clients

Industry/Entity Type

Massage Therapy

Coding

Coded - Design and coding required

Number of Pages Required

1 page

Font styles to use
Serif
Sans Serif

Requirements
Must have
• Please add or remove any information that would help the presentation of our website. Our logo is posted below, please include into the website.
• Please include a contact field that includes, kestrelwaymassage@fernmail.net,
• (206) 555-0148
• We have also included our own stock photos, as well as a photo of Paul and Lina. Please include a cropped photo of both massage therapists.

```html
<!DOCTYPE html>
<html lang="en">
<head>
<meta charset="utf-8">
<title>Kestrel Way Mobile Massage</title>
<link href="https://fonts.googleapis.com/css2?family=Courgette&family=Open+Sans:wght@400;600&family=Roboto:wght@400;500&display=swap" rel="stylesheet">
<style>
:root{
  --teal:#17bfb2;
  --blue:#1a2bb8;
  --ink:#1e1e1e;
  --muted:#555;
  --black:#000;
  --white:#fff;
  --band-light:#efefef;
  --script:'Courgette',cursive;
  --sans:'Roboto',sans-serif;
  --body:'Open Sans',sans-serif;
}
*{margin:0;padding:0;box-sizing:border-box}
html,body{width:1200px;height:3704px;overflow:hidden;background:var(--white);font-family:var(--sans);color:var(--ink)}
.page{position:relative;width:1200px;height:3704px}
.abs{position:absolute}

/* top bar */
.topbar{left:0;top:0;width:1200px;height:49px;background:var(--black);display:flex;justify-content:center;align-items:center;gap:22px}
.topbar .dot{width:11px;height:11px;border-radius:50%;background:var(--white)}
.topbar .dot.accent{background:var(--teal)}

/* nav */
.nav{left:0;top:49px;width:1200px;height:139px;background:var(--white)}
.nav a{position:absolute;top:64px;font-size:15px;color:var(--ink);text-decoration:none;transform:translateX(-50%);white-space:nowrap}
.nav a.active{color:var(--teal)}
.nav .active-bar{position:absolute;left:123px;top:0;width:104px;height:5px;background:var(--teal)}
.logo{left:536px;top:58px;width:128px;height:128px;border-radius:50%;background:var(--blue);border:4px solid var(--white);box-shadow:0 0 0 2px var(--blue);display:flex;align-items:center;justify-content:center;text-align:center;color:var(--white);font-family:var(--sans);font-weight:500;font-size:22px;line-height:1.1}

/* hero */
.hero{left:0;top:188px;width:1200px;height:469px;background:linear-gradient(120deg,#8a6a3c 0%,#d8b58c 35%,#f2e6d6 60%,#e7d3bd 80%,#b55a3e 100%)}
.hero-arrow{top:398px;width:46px;height:46px}
.hero-dots{left:562px;top:613px;display:flex;gap:10px;align-items:center}
.hero-dots span{width:9px;height:9px;border-radius:50%;background:var(--black)}
.hero-dots span.on{width:16px;height:16px;background:transparent;border:2px solid var(--black)}
.hero-line{top:621px;width:230px;height:1px;background:rgba(0,0,0,.35)}

/* section titles */
.title{font-family:var(--script);color:var(--teal);font-size:52px;font-weight:400;text-align:center;left:0;width:1200px;display:flex;align-items:center;justify-content:center;gap:28px;line-height:1.2;white-space:nowrap}
.title::before,.title::after{content:"";width:130px;height:2px;background:var(--teal);flex:none}
.title.light{color:var(--white)}
.title.light::before,.title.light::after{background:var(--white)}
.title.compact{gap:20px}
.title.compact::before,.title.compact::after{width:90px}

/* services */
.card{width:457px;height:193px;border:2px solid var(--teal);background:var(--white);overflow:hidden}
.card .photo{position:absolute;left:0;top:0;width:300px;height:100%}
.card h3{position:absolute;left:146px;top:40px;font-size:18px;font-weight:400;text-transform:uppercase;white-space:nowrap}
.card p{position:absolute;left:146px;top:76px;width:290px;font-family:var(--body);font-size:13px;line-height:20px;color:#333}

/* about */
.about{left:0;top:1264px;width:1200px;height:415px;background:linear-gradient(90deg,#3a2b22 0%,#4d3a2c 45%,#2d2119 100%)}
.about-text{left:79px;top:1440px;width:650px;color:var(--white);font-family:var(--body);font-size:15px;line-height:27px}
.polaroid{background:var(--white);padding:12px 12px 34px;box-shadow:0 6px 16px rgba(0,0,0,.5)}
.polaroid div{width:100%;height:100%}

/* rates */
.rate{width:182px;height:182px}
.rate .label{position:absolute;inset:0;display:flex;flex-direction:column;align-items:center;justify-content:center;font-family:var(--body);font-size:22px;line-height:28px;color:var(--ink)}

/* education */
.edu{left:0;top:2067px;width:1200px;height:414px;background:linear-gradient(100deg,#2a2f2a 0%,#4a4f4a 40%,#6a6762 62%,#1a1a1a 100%)}
.edu-text{left:150px;top:2208px;width:900px;text-align:center;color:var(--white);font-family:var(--body);font-size:14px;line-height:26px}
.btn{width:185px;height:60px;display:flex;align-items:center;justify-content:center;font-family:var(--sans);font-weight:500;font-size:18px;letter-spacing:.3px}
.btn.on-dark{left:506px;top:2350px;border:2px solid var(--white);color:var(--white)}

/* testimonial */
.quote-mark{left:0;width:1200px;top:2600px;text-align:center;font-family:Georgia,serif;font-size:64px;line-height:1;color:var(--ink)}
.testimonial-body{left:130px;top:2652px;width:940px;display:flex;flex-direction:column;align-items:center}
.quote{text-align:center;font-family:var(--body);font-size:14px;line-height:26px;color:#222}
.author{margin-top:8px;font-family:var(--body);font-weight:600;font-size:18px;line-height:24px}
.t-dots{margin-top:38px;display:flex;gap:12px}
.t-dots span{width:11px;height:11px;background:var(--black)}
.t-dots span.on{background:var(--white);border:2px solid var(--black)}

/* contact */
.contact{left:0;top:2869px;width:1200px;height:415px;background:linear-gradient(90deg,#dcdcda 0%,#f4f4f2 35%,#eeece8 60%,#d7d3cc 100%)}
.field-label{font-family:var(--body);font-size:14px;color:#222}
.field-line{height:1px;background:#555}
.btn.on-light{left:506px;top:3153px;border:2px solid #333;color:#222;background:transparent}

.infobar{left:0;top:3284px;width:1200px;height:106px;background:var(--band-light)}
.info{top:3322px;display:flex;align-items:center;gap:36px;font-family:var(--body);font-size:21px;color:#222;white-space:nowrap}

/* footer */
.footer{left:0;top:3390px;width:1200px;height:314px;background:var(--black)}
.footer-logo{left:547px;top:3438px;width:106px;height:106px;border-radius:50%;background:var(--blue);border:3px solid var(--white);display:flex;align-items:center;justify-content:center;text-align:center;color:var(--white);font-weight:500;font-size:18px;line-height:1.1}
.social{top:3566px;display:flex;gap:20px;left:462px}
.social span{width:58px;height:58px;border-radius:50%;border:2px solid var(--white);display:flex;align-items:center;justify-content:center}
.social span.fill{background:#1f3b3a;border-color:#2a5552}
.social span i{width:12px;height:12px;border-radius:50%;background:var(--white)}
.social span.fill i{background:var(--teal)}
.copy{left:0;width:1200px;top:3640px;text-align:center;font-family:var(--body);font-size:13px;color:var(--teal)}
</style>
</head>
<body>
<div class="page">

  <div class="abs topbar">
    <span class="dot"></span><span class="dot accent"></span><span class="dot"></span><span class="dot"></span>
  </div>

  <nav class="abs nav">
    <span class="active-bar"></span>
    <a class="active" style="left:175px">Home</a>
    <a style="left:300px">About us</a>
    <a style="left:437px">Our Rate</a>
    <a style="left:750px">Education</a>
    <a style="left:895px">Testimonial</a>
    <a style="left:1039px">Contact Us</a>
  </nav>
  <div class="abs logo">Kestrel<br>Way</div>

  <div class="abs hero" role="img" aria-label="Photo of a therapist giving a back massage to a client lying on a table with rose petals"></div>
  <svg class="abs hero-arrow" style="left:14px" viewBox="0 0 46 46"><rect x="1" y="1" width="44" height="44" fill="none" stroke="#fff" stroke-width="2"/><path d="M34 23H12M20 15l-8 8 8 8" fill="none" stroke="#fff" stroke-width="2"/></svg>
  <svg class="abs hero-arrow" style="left:1140px" viewBox="0 0 46 46"><rect x="1" y="1" width="44" height="44" fill="none" stroke="#fff" stroke-width="2"/><path d="M12 23h22M26 15l8 8-8 8" fill="none" stroke="#fff" stroke-width="2"/></svg>
  <span class="abs hero-line" style="left:310px"></span>
  <span class="abs hero-line" style="left:660px"></span>
  <div class="abs hero-dots"><span></span><span class="on"></span><span></span><span></span></div>

  <h2 class="abs title" style="top:710px">Services</h2>

  <div class="abs card" style="left:136px;top:802px">
    <div class="photo" role="img" aria-label="Photo of a therapist stretching a client's leg" style="background:linear-gradient(90deg,#9eb7bf 0%,#d9e3e4 45%,#fff 100%)"></div>
    <h3>Neuromuscular</h3>
    <p>Lorem ipsum dolor sit amet, consectetur adipiscing elit, sed do eiusmod tempor incididunt ut labore et dolore magna aliqua.</p>
  </div>
  <div class="abs card" style="left:605px;top:802px">
    <div class="photo" role="img" aria-label="Photo of a therapist assisting a standing client" style="background:linear-gradient(90deg,#b7a89a 0%,#e6e1dc 45%,#fff 100%)"></div>
    <h3>Spontaneous Muscle Release</h3>
    <p>Lorem ipsum dolor sit amet, consectetur adipiscing elit, sed do eiusmod tempor incididunt ut labore et dolore magna aliqua.</p>
  </div>
  <div class="abs card" style="left:136px;top:1005px">
    <div class="photo" role="img" aria-label="Photo of a therapist working on a client's leg" style="background:linear-gradient(90deg,#8a95a9 0%,#d5d6dc 45%,#fff 100%)"></div>
    <h3>Postural Restoration</h3>
    <p>Lorem ipsum dolor sit amet, consectetur adipiscing elit, sed do eiusmod tempor incididunt ut labore et dolore magna aliqua.</p>
  </div>
  <div class="abs card" style="left:605px;top:1005px">
    <div class="photo" role="img" aria-label="Photo of a therapist treating a client's shoulder" style="background:linear-gradient(90deg,#3f7a6a 0%,#c9ddd5 45%,#fff 100%)"></div>
    <h3>Medical Massage</h3>
    <p>Lorem ipsum dolor sit amet, consectetur adipiscing elit, sed do eiusmod tempor incididunt ut labore et dolore magna aliqua.</p>
  </div>

  <section class="abs about" role="img" aria-label="Dim background photo of a spa setting"></section>
  <h2 class="abs title light compact" style="left:74px;width:610px;top:1346px">Know About Us</h2>
  <p class="abs about-text">We are a male and female mobile massage team. Our names are Paul and Lina. Kestrel Way is a Seattle based mobile massage service. Our massage is offered to the community with a goal of facilitating balance within each individual. We specialize in integrated Pain management, and sports/medical massage therapy. Every client's first assessment is attended by our male and female massage therapist team.</p>
  <div class="abs polaroid" style="left:735px;top:1300px;width:228px;height:230px;transform:rotate(8deg)">
    <div role="img" aria-label="Photo of Paul" style="background:linear-gradient(135deg,#7d8ea3,#c2c9d2)"></div>
  </div>
  <div class="abs polaroid" style="left:862px;top:1385px;width:268px;height:262px;transform:rotate(6deg)">
    <div role="img" aria-label="Photo of Lina" style="background:linear-gradient(135deg,#8a8d67,#5c5a4a)"></div>
  </div>

  <h2 class="abs title" style="top:1732px">Our Rate</h2>
  <div class="abs rate" style="left:297px;top:1835px">
    <svg width="182" height="182" viewBox="0 0 182 182"><circle cx="91" cy="91" r="86" fill="none" stroke="var(--blue)" stroke-width="4"/><path d="M20 60A78 78 0 0 1 120 18" fill="none" stroke="var(--teal)" stroke-width="4"/></svg>
    <div class="label"><span>$ 75 / 60</span><span>Minutes</span></div>
  </div>
  <div class="abs rate" style="left:509px;top:1835px">
    <svg width="182" height="182" viewBox="0 0 182 182"><circle cx="91" cy="91" r="86" fill="none" stroke="var(--blue)" stroke-width="4"/><path d="M20 60A78 78 0 0 1 120 18" fill="none" stroke="var(--teal)" stroke-width="4"/></svg>
    <div class="label"><span>$ 95 / 90</span><span>Minutes</span></div>
  </div>
  <div class="abs rate" style="left:721px;top:1835px">
    <svg width="182" height="182" viewBox="0 0 182 182"><circle cx="91" cy="91" r="86" fill="none" stroke="var(--blue)" stroke-width="4"/><path d="M20 60A78 78 0 0 1 120 18" fill="none" stroke="var(--teal)" stroke-width="4"/></svg>
    <div class="label"><span>$ 120 / 120</span><span>Minutes</span></div>
  </div>

  <section class="abs edu" role="img" aria-label="Dark background photo of a studio wall with a painted sign and plants"></section>
  <h2 class="abs title light" style="top:2124px">Our Education</h2>
  <p class="abs edu-text">We are both Graduates of Venmora, school of massage therapy. We have continuing education in medical massage, myofacial release, trigger point therapy, postural restoration, anatomy, and spontaneous muscle release. Lina is also a Certified Yoga Instructor, which amplifies her experience with flexibility and strength as it pertains to each individual. Paul's passion is Massage, stretching, and strength training to encourage postural restoration and realignment.</p>
  <div class="abs btn on-dark">READ MORE</div>

  <h2 class="abs title" style="top:2518px">Testimonial</h2>
  <div class="abs quote-mark">&ldquo;</div>
  <div class="abs testimonial-body">
    <p class="quote">Lina and Paul at Kestrel Way are awesome! I recently had open heart surgery, and Lina worked on me to increase my range of motion while helping with the pinched nerve from my arm being in the same position for so long during my surgery. My wife drives a lot for work, and Paul has helped decrease her neck and lower back pain immensely. They are seriously the best therapists I have ever worked with</p>
    <div class="author">- Darcy T.</div>
    <div class="t-dots"><span></span><span class="on"></span><span></span><span></span><span></span><span></span></div>
  </div>

  <section class="abs contact" role="img" aria-label="Pale background photo of a bright massage room with tables by large windows"></section>
  <h2 class="abs title" style="top:2914px">Keep In Touch</h2>
  <span class="abs field-label" style="left:264px;top:3015px">Name</span>
  <span class="abs field-line" style="left:256px;top:3044px;width:349px"></span>
  <span class="abs field-label" style="left:636px;top:3015px">Email Id</span>
  <span class="abs field-line" style="left:622px;top:3044px;width:361px"></span>
  <span class="abs field-label" style="left:264px;top:3060px">Message</span>
  <span class="abs field-line" style="left:256px;top:3136px;width:727px"></span>
  <div class="abs btn on-light">SUBMIT</div>

  <div class="abs infobar"></div>
  <div class="abs info" style="left:252px">
    <svg width="20" height="20" viewBox="0 0 24 24"><path fill="var(--teal)" d="M6.6 10.8a15.1 15.1 0 0 0 6.6 6.6l2.2-2.2c.3-.3.7-.4 1-.2 1.1.4 2.3.6 3.6.6.6 0 1 .4 1 1V20c0 .6-.4 1-1 1A17 17 0 0 1 3 4c0-.6.4-1 1-1h3.5c.6 0 1 .4 1 1 0 1.3.2 2.5.6 3.6.1.3 0 .7-.2 1z"/></svg>
    <span>(206) 555-0148</span>
  </div>
  <div class="abs info" style="left:598px">
    <svg width="20" height="16" viewBox="0 0 24 18"><rect width="24" height="18" rx="2" fill="var(--teal)"/><path d="M1 2l11 8 11-8" fill="none" stroke="#fff" stroke-width="2"/></svg>
    <span>kestrelwaymassage@fernmail.net</span>
  </div>

  <footer class="abs footer"></footer>
  <div class="abs footer-logo">Kestrel<br>Way</div>
  <div class="abs social">
    <span class="fill"><i></i></span><span><i></i></span><span><i></i></span><span><i></i></span>
  </div>
  <p class="abs copy">© Kestrel Way mobile massage - 2015. All rights reserved.</p>

</div>
</body>
</html>
```